Nanny Share Ecommerce Website for Finding Childcare and Parents who need Childcare BrightPramHub.net

Our company needs an ecommerce website (BrightPramHub.net) for a US subscription based service strictly for nanny sharing that connects families and caregivers. The website would allow families to connect with one another as well as to search for nannies. The service would be searchable for other families by location (by radius or zip code), children demographic (age range/gender/special needs), days of week or times, after school care, school closure days (holidays), etc. The service would also be searchable for nannies based on gender, provider age range, years experience, language, hourly rate, transportation available, certification (CPR first aid), education etc. The search fields would be searchable and sortable and allow to connect with the provider (after paying subscription fee). The service would be similar to tendlyfolk.net in that it would allow for families and caregivers to post photos as well as a short bio of the themselves. There would also be a feedback/star rating mechanism to rate caregivers who have performed work for families (viewable to public). The service would be free for nannies to post their bios and only a subscription based service for families to connect with other families or with caregivers (able to view bio but need service to connect). There will be a short bio on the benefits of nanny sharing (reduced cost, increased flexibility for parents, reduced illness, increased socialization with other children vs. sole nanny), as well as Q&A section with best practices.

Target Market(s)

Families, Nannies

Industry/Entity Type

Childcare

Logo Text

Bright Pram Hub

Coding

Coded - Design and coding required

Number of Pages Required

5+ page

Requirements
Must have
• Searchable (need to be able to search for families as well as nannies), responsive, functional, easy to use, add value to families and nannies. Needs to be able to collect payment for subscription.
Nice to have
• Optimized for mobile, SEO optimized

```html
<!DOCTYPE html>
<html lang="en">
<head>
<meta charset="utf-8">
<title>Bright Pram Hub – Nanny Sharing</title>
<link rel="stylesheet" href="https://fonts.googleapis.com/css2?family=Lato:wght@400;700;900&family=Open+Sans:wght@400;600;700&display=swap">
<style>
:root{
  --pink:#ec0c8c;
  --blue:#18a8ea;
  --blue-dark:#1f6fb8;
  --ink:#222;
  --text:#555;
  --muted:#777;
  --soft-pink:#fdeef6;
  --soft-blue:#eef7fc;
  --reviews-bg:#f7f7f9;
  --footer-bg:#1c1c1c;
  --bar-bg:#0b0b0b;
  --white:#fff;
}
*{box-sizing:border-box;margin:0;padding:0}
html,body{width:1200px;height:3719px;overflow:hidden}
body{position:relative;background:var(--white);font-family:"Open Sans",Arial,sans-serif;color:var(--text)}
.abs{position:absolute}
ul{list-style:none}

/* header */
.site-header{position:absolute;left:0;top:0;width:1200px;height:112px;background:var(--white)}
.brand{position:absolute;left:99px;top:38px;display:flex;align-items:center;gap:10px}
.brand-dot{width:30px;height:30px;border-radius:50%;background:var(--pink)}
.brand-name{font-family:"Lato",sans-serif;font-weight:900;font-size:30px;color:var(--pink)}
.top-contact{position:absolute;top:25px;right:100px;display:flex;gap:32px;font-size:14px;color:var(--ink)}
.top-contact span{display:flex;align-items:center;gap:9px}
.main-nav{position:absolute;top:64px;right:99px;display:flex;gap:20px;font-size:15.5px;color:var(--ink)}
.main-nav .active{color:var(--blue)}

/* hero */
.hero{position:absolute;left:0;top:112px;width:1200px;height:570px}
.hero-photo{position:absolute;inset:0;background:linear-gradient(100deg,#d8c9c3 0%,#efe6e2 30%,#f7efe9 55%,#e9ddd6 80%,#dcd0ca 100%)}
.hero-title{position:absolute;top:136px;left:0;width:1200px;text-align:center;font-family:"Lato",sans-serif;font-weight:900;font-size:84px;color:var(--pink);letter-spacing:1px}
.finder{position:absolute;left:159px;top:578px;width:882px;height:203px;background:var(--blue);padding:9px}
.finder-inner{border:1.5px solid rgba(255,255,255,.85);height:100%;display:flex;position:relative}
.finder-inner::after{content:"";position:absolute;left:50%;top:22px;bottom:22px;border-left:1px solid rgba(255,255,255,.6)}
.finder-col{width:50%;padding:26px 0 0 89px;color:var(--white)}
.finder-col h3{font-family:"Lato",sans-serif;font-weight:400;font-size:21px;margin-bottom:10px}
.finder-col p{font-size:13px;line-height:21px;width:260px}
.btn{display:inline-block;background:var(--pink);color:var(--white);font-family:"Lato",sans-serif;font-weight:700;font-size:13px;text-transform:uppercase;text-align:center}
.finder-col .btn{margin-top:16px;padding:10px 26px}

/* offer */
.section-title{font-family:"Lato",sans-serif;font-weight:700;font-size:31px;color:var(--ink)}
.offer-title{top:852px;left:0;width:1200px;text-align:center}
.offer-text{top:908px;left:200px;width:800px;text-align:center;font-size:13.5px;line-height:33px;color:var(--muted)}
.hexes{position:absolute;left:0;top:1030px}
.view-all-offer{top:1594px;left:486px;width:228px;height:45px;line-height:45px;text-transform:none;font-size:13.5px}

/* benefits */
.benefits{position:absolute;left:0;top:1723px;width:1200px;height:540px;background:linear-gradient(90deg,#f2f2f4,#fafafb 60%,#f3f3f5)}
.benefits-photo{position:absolute;left:0;top:0;width:600px;height:540px;background:linear-gradient(90deg,#d9dde2 0%,#e8e2dc 40%,#ece7e2 75%,rgba(245,245,247,0) 100%)}
.benefits-title{top:58px;left:565px}
.benefit{position:absolute;left:565px;width:560px;display:flex;gap:20px}
.benefit svg{flex:none;margin-top:2px}
.benefit h4{font-family:"Open Sans",sans-serif;font-weight:700;font-size:14.5px;color:var(--ink);margin-bottom:4px}
.benefit p{font-size:13px;line-height:22px;color:var(--text)}

/* reviews */
.reviews{position:absolute;left:0;top:2263px;width:1200px;height:444px;background:var(--reviews-bg)}
.reviews-title{top:72px;left:402px}
.avatar{position:absolute;border-radius:50%;border:3px solid var(--white);box-shadow:0 2px 6px rgba(0,0,0,.15)}
.review-card{position:absolute;left:389px;top:139px;width:469px;height:226px;background:var(--white);border:1px solid #e2e2e2;box-shadow:0 3px 10px rgba(0,0,0,.08);padding:24px 26px}
.review-card::before{content:"";position:absolute;left:-13px;top:180px;width:24px;height:24px;background:var(--white);border-left:1px solid #e2e2e2;border-bottom:1px solid #e2e2e2;transform:rotate(45deg)}
.review-card h4{font-weight:600;font-size:15px;color:var(--ink);margin-bottom:10px}
.review-card p{font-size:13.5px;line-height:26px;color:var(--muted)}
.review-card .by{margin-top:16px;font-size:12.5px;font-weight:700;color:var(--blue-dark);line-height:18px}
.review-card .place{font-size:12px;color:var(--muted);line-height:20px}
.rating{position:absolute;left:942px;top:2424px;width:100px;height:100px;border-radius:50%;background:var(--pink);border:4px solid #f3c0dd;color:var(--white);text-align:center;padding-top:16px}
.rating b{display:block;font-family:"Lato",sans-serif;font-size:29px;font-weight:700;line-height:32px}
.rating i{font-style:normal;font-size:12px;letter-spacing:1px}
.rating-meta{position:absolute;left:872px;top:2554px;width:240px;text-align:center;font-size:14px;line-height:22px}
.rating-meta strong{color:var(--ink)}
.rating-meta span{color:var(--blue-dark)}

/* faq */
.faq-title{top:2782px;left:0;width:1200px;text-align:center}
.faq-item{position:absolute;width:466px;height:87px;display:flex;padding:20px 16px 0 30px;font-size:13px;line-height:24px;color:var(--text)}
.faq-item .mark{width:26px;flex:none;font-weight:600;color:var(--ink)}
.faq-q{left:117px;background:var(--soft-pink)}
.faq-a{left:617px;background:var(--soft-blue)}
.view-all-faq{top:3218px;left:543px;width:114px;height:42px;line-height:42px;text-transform:none;font-size:13.5px}

/* footer */
.site-footer{position:absolute;left:0;top:3342px;width:1200px;height:307px;background:var(--footer-bg);color:var(--white)}
.footer-brand{position:absolute;left:99px;top:60px;display:flex;align-items:center;gap:10px}
.footer-brand .brand-name{color:var(--white);font-size:28px}
.footer-brand .brand-dot{background:var(--white)}
.footer-about{position:absolute;left:99px;top:166px;width:273px;font-size:13px;line-height:26px;text-align:justify}
.footer-col{position:absolute;top:58px}
.footer-col h5{font-family:"Lato",sans-serif;font-weight:400;font-size:20px;margin-bottom:20px;letter-spacing:.5px}
.footer-col li{font-size:12.5px;line-height:26px;position:relative;padding-left:22px}
.footer-col .links li::before{content:"";position:absolute;left:4px;top:11px;width:6px;height:6px;border-radius:50%;background:var(--blue)}
.contact-list li{display:flex;align-items:center;gap:12px;padding-left:0;line-height:30px;font-size:13px}
.social{position:absolute;left:994px;top:245px;display:flex;gap:13px}
.social span{width:26px;height:26px}
.bottom-bar{position:absolute;left:0;top:3649px;width:1200px;height:70px;background:var(--bar-bg);color:#ddd;font-size:12.5px;text-align:center;line-height:70px}
</style>
</head>
<body>

<header class="site-header">
  <div class="brand"><span class="brand-dot"></span><span class="brand-name">Bright Pram Hub</span></div>
  <div class="top-contact">
    <span>
      <svg width="15" height="11" viewBox="0 0 15 11"><rect width="15" height="11" rx="1" fill="#18a8ea"/><path d="M0 1l7.5 5L15 1" stroke="#fff" stroke-width="1.4" fill="none"/></svg>
      info@brightpramhub.net
    </span>
    <span>
      <svg width="13" height="13" viewBox="0 0 24 24"><path fill="#18a8ea" d="M6.6 10.8a15 15 0 006.6 6.6l2.2-2.2c.3-.3.7-.4 1-.2 1.1.4 2.3.6 3.6.6.6 0 1 .4 1 1V20c0 .6-.4 1-1 1A17 17 0 013 4c0-.6.4-1 1-1h3.5c.6 0 1 .4 1 1 0 1.3.2 2.5.6 3.6.1.3 0 .7-.2 1z"/></svg>
      (555) 210 4380
    </span>
  </div>
  <nav class="main-nav">
    <span class="active">Home</span><span>About Us</span><span>Services</span><span>Nannies Care ▾</span><span>Blog</span><span>Faq</span><span>Contact Us</span>
  </nav>
</header>

<section class="hero">
  <div class="hero-photo" role="img" aria-label="Photo of a mother holding a smiling baby"></div>
  <h1 class="hero-title">BRIGHT PRAM HUB</h1>
</section>

<div class="finder">
  <div class="finder-inner">
    <div class="finder-col">
      <h3>I need a care giver</h3>
      <p>But I must explain to you how all this mistaken idea of denouncing</p>
      <span class="btn">Find Care</span>
    </div>
    <div class="finder-col" style="padding-left:74px">
      <h3>Let's get started</h3>
      <p>But I must explain to you how all this mistaken idea of denouncing</p>
      <span class="btn">Search Nanny</span>
    </div>
  </div>
</div>

<h2 class="section-title abs offer-title">What We Offer?</h2>
<p class="abs offer-text">Sed ut perspiciatis unde omnis iste natus error sit voluptatem tium remque laudantium, totam rem aperiam, eaque ipsa quae quasi architecto beatae vitae dicta sunt explicabo. Nemo enim ipsum voluptatem quia voluptas sit aspernatur odit aut fugit, sed quia quuntur magni dolores eos qui ratione voluptatem sequi nesciunt</p>

<svg class="hexes" width="1200" height="500" viewBox="0 0 1200 500">
  <g role="img" aria-label="Photo of a caregiver playing with a little girl">
    <polygon points="465,123 532,7 668,7 735,123 668,239 532,239" fill="#e6cfc4"/>
  </g>
  <g role="img" aria-label="Photo of a nurse with a senior woman">
    <polygon points="230,250 297,134 433,134 500,250 433,366 297,366" fill="#c9b7a8"/>
  </g>
  <g role="img" aria-label="Photo of a woman caring for a potted plant at home">
    <polygon points="465,377 532,261 668,261 735,377 668,493 532,493" fill="#b9957a"/>
  </g>
  <g>
    <polygon points="700,250 767,134 903,134 970,250 903,366 767,366" fill="#e0248e"/>
    <text x="835" y="247" text-anchor="middle" fill="#fff" font-family="Lato,sans-serif" font-size="24">Pet Care</text>
    <text x="835" y="276" text-anchor="middle" fill="#fff" font-family="Open Sans,sans-serif" font-size="12.5" text-decoration="underline">View Details</text>
  </g>
</svg>

<span class="btn abs view-all-offer">Click Here To View All &nbsp;➜</span>

<section class="benefits">
  <div class="benefits-photo" role="img" aria-label="Photo of a young woman hugging a senior woman"></div>
  <h2 class="section-title abs benefits-title">Benefits of Nanny Sharing</h2>
  <div class="benefit" style="top:142px">
    <svg width="40" height="40" viewBox="0 0 40 40"><circle cx="20" cy="20" r="13" fill="none" stroke="#1f6fb8" stroke-width="3"/><path d="M20 12v16M15 17h8a3 3 0 010 6h-6" stroke="#1f6fb8" stroke-width="2.5" fill="none"/><path d="M3 20h4M33 20h4" stroke="#1f6fb8" stroke-width="3"/></svg>
    <div><h4>Reduced cost</h4><p>At vero eos et accusamus et iusto odio dignissimos ducimus qui blanditiis<br>praesentium voluptatum deleniti</p></div>
  </div>
  <div class="benefit" style="top:232px">
    <svg width="40" height="40" viewBox="0 0 40 40"><rect x="5" y="26" width="5" height="10" fill="#1f6fb8"/><rect x="13" y="20" width="5" height="16" fill="#1f6fb8"/><rect x="21" y="23" width="5" height="13" fill="#1f6fb8"/><rect x="29" y="14" width="5" height="22" fill="#1f6fb8"/><path d="M5 19l9-7 8 4 12-10" stroke="#1f6fb8" stroke-width="2.5" fill="none"/></svg>
    <div><h4>Increased flexibility for parents</h4><p>At vero eos et accusamus et iusto odio dignissimos ducimus qui blanditiis<br>praesentium voluptatum deleniti</p></div>
  </div>
  <div class="benefit" style="top:323px">
    <svg width="40" height="40" viewBox="0 0 40 40"><circle cx="18" cy="6" r="4" fill="#1f6fb8"/><path d="M17 12v12h10l4 9" stroke="#1f6fb8" stroke-width="3.5" fill="none"/><circle cx="17" cy="27" r="9" fill="none" stroke="#1f6fb8" stroke-width="3"/></svg>
    <div><h4>Reduced illness</h4><p>At vero eos et accusamus et iusto odio dignissimos ducimus qui blanditiis<br>praesentium voluptatum deleniti</p></div>
  </div>
  <div class="benefit" style="top:414px">
    <svg width="40" height="40" viewBox="0 0 40 40"><circle cx="20" cy="12" r="6" fill="#1f6fb8"/><circle cx="8" cy="16" r="4.5" fill="#1f6fb8"/><circle cx="32" cy="16" r="4.5" fill="#1f6fb8"/><path d="M9 34a11 11 0 0122 0z" fill="#1f6fb8"/><path d="M0 32a8 8 0 0114-6M40 32a8 8 0 00-14-6" fill="#1f6fb8"/></svg>
    <div><h4>Increased socialization</h4><p>At vero eos et accusamus et iusto odio dignissimos ducimus qui blanditiis<br>praesentium voluptatum deleniti</p></div>
  </div>
</section>

<section class="reviews">
  <h2 class="section-title abs reviews-title">Real Reviews</h2>
  <div class="avatar" role="img" aria-label="Portrait of a reviewer" style="left:270px;top:129px;width:60px;height:60px;background:#c9a58c"></div>
  <div class="avatar" role="img" aria-label="Portrait of the featured reviewer" style="left:134px;top:184px;width:114px;height:114px;background:#b48a6e"></div>
  <div class="avatar" role="img" aria-label="Portrait of a reviewer" style="left:273px;top:278px;width:84px;height:84px;background:#a88a78"></div>
  <div class="review-card">
    <h4>Really satisfied with your service</h4>
    <p>On the other hand, we denounce with righteous indignation and dislike men who are so beguiled and demoralized by the charms of pleasure of the moment.</p>
    <div class="by">By Maren</div>
    <div class="place">Sydney, Australia</div>
  </div>
</section>
<div class="rating"><b>4.5</b><i>★★★★★</i></div>
<div class="rating-meta"><strong>By 230,34 Views</strong><br><span>Blanditiis praesentium</span></div>

<h2 class="section-title abs faq-title">Faq</h2>
<div class="faq-item faq-q" style="top:2861px"><span class="mark">Q)</span><span>At vero eos et accusamus et iusto odio dignissimos mus qui blanditiis praesentium ?</span></div>
<div class="faq-item faq-a" style="top:2861px"><span class="mark">A)</span><span>At vero eos et accusamus et iusto odio dignissimos mus qui blanditiis praesentium</span></div>
<div class="faq-item faq-q" style="top:2980px"><span class="mark">Q)</span><span>At vero eos et accusamus et iusto odio dignissimos mus qui blanditiis praesentium ?</span></div>
<div class="faq-item faq-a" style="top:2980px"><span class="mark">A)</span><span>At vero eos et accusamus et iusto odio dignissimos mus qui blanditiis praesentium</span></div>
<div class="faq-item faq-q" style="top:3099px"><span class="mark">Q)</span><span>At vero eos et accusamus et iusto odio dignissimos mus qui blanditiis praesentium ?</span></div>
<div class="faq-item faq-a" style="top:3099px"><span class="mark">A)</span><span>At vero eos et accusamus et iusto odio dignissimos mus qui blanditiis praesentium</span></div>
<span class="btn abs view-all-faq">View All</span>

<footer class="site-footer">
  <div class="footer-brand"><span class="brand-dot"></span><span class="brand-name">Bright Pram Hub</span></div>
  <p class="footer-about">Lumora has been providing the radiation therapy community with innovative, quality and precise products for internal, external and brachytherapy</p>
  <div class="footer-col" style="left:426px">
    <h5>QUICK LINKS</h5>
    <ul class="links"><li>Home</li><li>About Us</li><li>Services</li><li>Nannies Care</li><li>Blog</li><li>Faq</li></ul>
  </div>
  <div class="footer-col" style="left:625px">
    <h5>OTHER LINKS</h5>
    <ul class="links"><li>Child Care</li><li>Senior Care</li><li>Adult Care</li><li>Home Care</li><li>NightDay</li><li>Contact Us</li></ul>
  </div>
  <div class="footer-col" style="left:823px">
    <h5>CONTACT US</h5>
    <ul class="contact-list">
      <li><svg width="12" height="16" viewBox="0 0 12 16"><path d="M6 0a6 6 0 00-6 6c0 4.5 6 10 6 10s6-5.5 6-10a6 6 0 00-6-6z" fill="#18a8ea"/><circle cx="6" cy="6" r="2.2" fill="#1c1c1c"/></svg>820 Maple Grove Ave, Dayton, OH 45402</li>
      <li><svg width="14" height="11" viewBox="0 0 14 11"><rect width="14" height="11" rx="1" fill="#18a8ea"/><path d="M0 1l7 5 7-5" stroke="#1c1c1c" stroke-width="1.3" fill="none"/></svg>info@brightpramhub.net</li>
      <li><svg width="13" height="13" viewBox="0 0 24 24"><path fill="#18a8ea" d="M6.6 10.8a15 15 0 006.6 6.6l2.2-2.2c.3-.3.7-.4 1-.2 1.1.4 2.3.6 3.6.6.6 0 1 .4 1 1V20c0 .6-.4 1-1 1A17 17 0 013 4c0-.6.4-1 1-1h3.5c.6 0 1 .4 1 1 0 1.3.2 2.5.6 3.6.1.3 0 .7-.2 1z"/></svg>Toll Free: (555) 210 4380</li>
    </ul>
  </div>
  <div class="social"><span style="background:#3b5998"></span><span style="background:#1da1f2"></span><span style="background:#dd4b39"></span></div>
</footer>
<div class="bottom-bar">©Copyright - 2018 BRIGHTPRAMHUB, All Rights Reserved</div>

</body>
</html>
```